Business cards to launch an education platform

Hi,
I am looking at having new business cards designed.
I am a startup, developing a web platform for schools and university, the education world. It's an online assessment system.
I would like a card that looks classy, and that is using the colors and the font of my logo.

I have attached:
1) my logo
2) A business card that I have designed quickly so you can have all the information required in the card, but I really don't like it.
3) The font that I am using (Lato Regular) to design my web platform
4) Some screenshots of my web platform so you can have a look at the style that I have.

Target Market(s)

Major market: Education system: Schools and university
Minor markets: Business in general

Industry/Entity Type

Business

Contact Information for Business Card

Clara Fenwick
Director

M: 0437 518 902
E: clara.fenwick@amberLoomSystems.com.au

Requirements
Must have
• The colors of my logo

```html
<!DOCTYPE html>
<html lang="en">
<head>
<meta charset="utf-8">
<title>Amber Loom systems — Business Cards</title>
<link rel="stylesheet" href="https://fonts.googleapis.com/css2?family=Lato:wght@400;700&display=swap">
<style>
  :root {
    --canvas-bg: #e9ebee;
    --card-white: #ffffff;
    --brand-navy: #173a6b;
    --band-top: #0b77cc;
    --band-bottom: #0c4a8c;
    --text-on-band: #ffffff;
    --shadow: rgba(20, 40, 70, 0.22);
  }
  * { box-sizing: border-box; margin: 0; padding: 0; }
  html, body {
    width: 1200px;
    height: 900px;
    overflow: hidden;
    background: var(--canvas-bg);
    font-family: "Lato", Arial, sans-serif;
  }
  .canvas { position: relative; width: 1200px; height: 900px; }

  .card {
    position: absolute;
    background: var(--card-white);
    box-shadow: 0 6px 18px var(--shadow);
    overflow: hidden;
  }
  .band {
    position: absolute;
    left: 0;
    right: 0;
    background: linear-gradient(to bottom, var(--band-top), var(--band-bottom));
  }

  /* Front */
  .card-front { left: 78px; top: 35px; width: 588px; height: 363px; }
  .card-front .band { top: 181px; bottom: 0; }
  .front-brand { position: absolute; left: 30px; top: 33px; display: flex; align-items: center; }
  .brand-mark { width: 100px; height: 100px; background: var(--brand-navy); flex: none; }
  .front-brand .brand-name {
    margin-left: 24px;
    color: var(--brand-navy);
    font-weight: 400;
    line-height: 1.05;
  }
  .brand-name .line-main { display: block; font-size: 38px; letter-spacing: 2px; }
  .brand-name .line-sub { display: block; font-size: 26px; letter-spacing: 1.5px; }

  .holder { position: absolute; left: 31px; top: 202px; color: var(--text-on-band); }
  .holder-name { font-size: 22px; font-weight: 400; line-height: 1.1; }
  .holder-role { font-size: 16px; line-height: 1.2; }

  .contact-list { position: absolute; left: 32px; top: 282px; list-style: none; color: var(--text-on-band); font-size: 16px; }
  .contact-list li { display: flex; align-items: center; height: 25px; }
  .contact-list svg { width: 12px; height: 12px; margin-right: 7px; fill: var(--text-on-band); }

  /* Back */
  .card-back { left: 388px; top: 505px; width: 567px; height: 352px; }
  .card-back .band { top: 110px; height: 131px; }
  .back-brand {
    position: absolute;
    right: 125px;
    top: 36px;
    display: flex;
    align-items: center;
  }
  .back-brand .brand-name { color: var(--text-on-band); text-align: right; line-height: 1.1; }
  .back-brand .line-main { font-size: 31px; letter-spacing: 2.5px; }
  .back-brand .line-sub { font-size: 21px; letter-spacing: 2px; }
  .divider { width: 2px; height: 108px; background: var(--text-on-band); margin: 0 0 0 14px; position: relative; top: 0; }
  .back-mark { position: absolute; right: 125px; top: 26px; }
  .back-mark .brand-mark { position: absolute; left: 18px; top: 0; width: 84px; height: 84px; background: var(--text-on-band); }
</style>
</head>
<body>
<main class="canvas">

  <section class="card card-front" aria-label="Business card front">
    <div class="front-brand">
      <div class="brand-mark" aria-hidden="true"></div>
      <div class="brand-name">
        <span class="line-main">AMBER</span>
        <span class="line-sub">Loom systems</span>
      </div>
    </div>
    <div class="band">
    </div>
    <div class="holder">
      <h1 class="holder-name">Clara Fenwick</h1>
      <p class="holder-role">Director</p>
    </div>
    <ul class="contact-list">
      <li>
        <svg viewBox="0 0 24 24" aria-hidden="true"><path d="M6.6 10.8a15.1 15.1 0 0 0 6.6 6.6l2.2-2.2a1 1 0 0 1 1-.25 11.4 11.4 0 0 0 3.6.57 1 1 0 0 1 1 1V20a1 1 0 0 1-1 1A17 17 0 0 1 3 4a1 1 0 0 1 1-1h3.5a1 1 0 0 1 1 1c0 1.25.2 2.45.57 3.6a1 1 0 0 1-.25 1z"/></svg>
        0437 518 902
      </li>
      <li>
        <svg viewBox="0 0 24 24" aria-hidden="true"><path d="M2 5h20v14H2z M2 5l10 8 10-8" stroke="#0c4a8c" stroke-width="1.6"/></svg>
        clara.fenwick@amberLoomSystems.com.au
      </li>
    </ul>
  </section>

  <section class="card card-back" aria-label="Business card back">
    <div class="band">
      <div class="back-brand">
        <div class="brand-name">
          <span class="line-main">AMBER</span>
          <span class="line-sub">Loom systems</span>
        </div>
        <div class="divider" aria-hidden="true"></div>
      </div>
      <div class="back-mark" aria-hidden="true" style="right:20px;top:13px;width:110px;height:100px;">
        <div class="brand-mark"></div>
      </div>
    </div>
  </section>

</main>
</body>
</html>
```